Business Cards for new orthopaedic surgery practice

My husband and I are starting our own orthopaedic surgery practice. We are looking for a business card that is uniform, but one will have my name/title and the other will have his. You can just create one design with my name on it for now. But when I choose your design as the winning design I will ask that you add another copy with his name/title.

We are looking for classy, simple, elite all in one. We like dark blues/a little gold/yellow. Something that goes with our logo. We want our logo incorporated. Here is all the info you need:
Business name: RV Bone & Vitality Center
Location: 38517 North Willowmere Ave
Cedar Hollow, FL 33490
Phone: 954-218-4063
Fax: 954-582-7341
Email: info@myrvbonecare.example

Names: Lydia Vance, M.D.
Board Certified Hand and Upper Extremity Surgeon

Ebo Dansu, M.D.
Board Certified Hip & Knee Replacement/General Orthopaedic Surgeon

Can decide what you want to put on the back. Maybe a slogan:
Grounded in Care. Centered on You

I am just going to upload our logo. The only thing is if we select you as the winning design, the location, and phone numbers may change. We will need your help to update that once fully solidified.

Industry/Entity Type

Medical

Contact Information for Business Card

Colors
0054AA
0677BA
7BADD7
CADEEF
E8F1F8
0094D4
00A9DD
6FCCEA
C7EBF8
E9F6FB

Requirements
Must have
• class, appeal,
Should not have
• We want to air on the side of masculine if we are looking at masculine vs. feminine feel. But we still want it classy, sophisticated, and something we will love

```html
<!DOCTYPE html>
<html lang="en">
<head>
<meta charset="utf-8">
<title>RV Bone &amp; Vitality Center – Business Card</title>
<link rel="stylesheet" href="https://fonts.googleapis.com/css2?family=Crimson+Text:wght@400;600&display=swap">
<style>
  :root {
    --stage: #4a4a4a;
    --front-bg: #17bbe2;
    --back-bg: #223b80;
    --navy-ink: #223b80;
    --cyan-ink: #1fb8e6;
    --white-ink: #ffffff;
  }
  * { box-sizing: border-box; margin: 0; padding: 0; }
  html, body {
    width: 1200px; height: 694px; overflow: hidden;
    background: var(--stage);
    font-family: "Crimson Text", Georgia, serif;
  }
  .stage {
    position: relative; width: 1200px; height: 694px;
    display: flex; align-items: center; justify-content: center; gap: 40px;
  }
  .card {
    position: relative; width: 540px; height: 309px;
    border-radius: 22px; overflow: hidden;
    box-shadow: 0 14px 30px rgba(0,0,0,.35);
  }

  /* Front */
  .card-front { background: var(--front-bg); color: var(--navy-ink); }
  .front-brand {
    position: absolute; left: 0; right: 0; top: 92px;
    text-align: center;
  }
  .front-brand .brand-name {
    display: inline-flex; align-items: center; gap: 12px;
    font-size: 30px; font-weight: 600; text-transform: uppercase; letter-spacing: 1px;
  }
  .brand-dot {
    width: 14px; height: 14px; border-radius: 50%; background: var(--navy-ink);
  }
  .front-rule {
    display: flex; align-items: center; justify-content: center; gap: 12px;
    margin-top: 10px; font-size: 15px; letter-spacing: 3px; text-transform: uppercase;
  }
  .front-rule::before, .front-rule::after {
    content: ""; width: 90px; height: 1.5px; background: var(--navy-ink);
  }
  .slogan {
    position: absolute; left: 0; right: 0; bottom: 56px;
    text-align: center; font-size: 13px; letter-spacing: 3px; text-transform: uppercase;
  }

  /* Back */
  .card-back { background: var(--back-bg); color: var(--white-ink); }
  .back-brand {
    position: absolute; top: 34px; right: 36px;
    display: flex; align-items: center; gap: 8px;
    font-size: 17px; font-weight: 600; text-transform: uppercase; letter-spacing: .5px;
    color: var(--white-ink);
  }
  .back-brand .brand-dot { width: 10px; height: 10px; background: var(--white-ink); }
  .person { position: absolute; left: 36px; top: 112px; }
  .person-name {
    color: var(--cyan-ink); font-size: 21px; font-weight: 600;
    text-transform: uppercase; letter-spacing: .5px;
  }
  .person-title { font-size: 13px; font-weight: 600; line-height: 1.2; margin-top: 3px; }
  .hours {
    position: absolute; right: 36px; top: 150px; text-align: right;
    font-size: 13px; font-weight: 600; line-height: 1.3;
  }
  .hours .closed { color: var(--cyan-ink); }
  .contact { position: absolute; left: 36px; bottom: 26px; font-size: 13px; font-weight: 600; line-height: 1.25; }
  .address { margin-bottom: 8px; }
  .contact-row { display: flex; align-items: center; gap: 8px; }
  .contact-row svg { width: 12px; height: 12px; fill: var(--cyan-ink); flex: none; }
</style>
</head>
<body>
<main class="stage">

  <section class="card card-front" aria-label="Card front">
    <div class="front-brand">
      <div class="brand-name"><span class="brand-dot"></span>RV Bone &amp; Vitality</div>
      <div class="front-rule">Center</div>
    </div>
    <p class="slogan">Grounded in Care. Centered on You</p>
  </section>

  <section class="card card-back" aria-label="Card back">
    <div class="back-brand"><span class="brand-dot"></span>RV Bone &amp; Vitality Center</div>

    <div class="person">
      <h1 class="person-name">Lydia Vance, M.D.</h1>
      <p class="person-title">Board Certified Hand<br>and Upper Extremity Surgeon</p>
    </div>

    <div class="hours">
      <p>Opening Hours</p>
      <p>Monday to Friday - 9:00 AM - 5:00 PM</p>
      <p class="closed">Saturday / Sunday Closed</p>
    </div>

    <div class="contact">
      <p class="address">38517 North Willowmere Ave<br>Cedar Hollow, FL 33490</p>
      <p class="contact-row">
        <svg viewBox="0 0 12 12" aria-hidden="true"><path d="M2.5 1 4.5 1 5.3 3.4 4 4.4a7 7 0 0 0 3.6 3.6L8.6 6.7 11 7.5v2c0 .8-.7 1.5-1.5 1.5A8.5 8.5 0 0 1 1 2.5C1 1.7 1.7 1 2.5 1z"/></svg>
        954-218-4063
      </p>
      <p class="contact-row">
        <svg viewBox="0 0 12 12" aria-hidden="true"><path d="M3 1h6v3H3zM1 5h10v5H9V8H3v2H1zM3.5 9h5v2.5h-5z"/></svg>
        954-582-7341
      </p>
      <p class="contact-row">
        <svg viewBox="0 0 12 12" aria-hidden="true"><path d="M1 2h10v8H1zM2 3.2v.4L6 6.4l4-2.8v-.4zM2 4.8V9h8V4.8L6 7.6z"/></svg>
        info@myrvbonecare.example
      </p>
    </div>
  </section>

</main>
</body>
</html>
```